Drabek Partners envision a corporate 22 year old theme with as many features functional

We need an interactive website designed.
Fully interactive with social media
Fully Interactive with Live content
you should map out how you'd like the website to work. This is important both for user experience and for SEO, since Zorvia considers the content and structure of a site when it ranks
Crucial Business Information
Keep text to a minimum when it comes to your mission statement, because you should be writing things so people can skim — we all have short attention spans.
Depending on your business, you should have a few things on your website that fall into the realm of "information." Tailor your site so that it offers the information users are likely to be looking for.
Content
Clear Navigation
Security
Social Media Intergration
Mobile Ready
Feel free to forgo these things on your website:
Music
Flash
Anything that autoplays,
Extraneous information and media
Industry/Entity Type
Media
Contact Information for Business Card
Coding
Coded - Design and coding required
Number of Pages Required
1 page
Other font styles liked:
- as per uploaded Guidelines
Requirements
Must have
Nice to have
Should not have

```html
<!DOCTYPE html>
<html lang="en">
<head>
<meta charset="utf-8">
<title>Drabek Partners — people, capital, strategy</title>
<link rel="stylesheet" href="https://fonts.googleapis.com/css2?family=Nunito:wght@800&family=Open+Sans:wght@400;600;700&family=Ropa+Sans&display=swap">
<style>
:root{
  --green:#27b27f;
  --green-dark:#1d9a6c;
  --ink:#1b1b1b;
  --text:#3c3c3c;
  --muted:#7a7a7a;
  --nav:#1f2b2a;
  --frame:#e8e8e8;
  --panel:#f3f3f3;
  --white:#ffffff;
  --rule:#d8d8d8;
}
*{box-sizing:border-box;margin:0;padding:0}
html,body{width:1200px;height:2799px;overflow:hidden}
body{background:var(--frame);font-family:"Open Sans",Arial,sans-serif;color:var(--text)}
.page{position:relative;width:1172px;height:2785px;margin:0 14px;background:var(--white)}

/* header */
.site-header{position:relative;height:111px}
.brand{position:absolute;left:24px;top:22px;font-family:"Nunito",Arial,sans-serif;font-weight:800;color:var(--ink);line-height:.9}
.brand .line1{display:block;font-size:44px;letter-spacing:-1px}
.brand .line2{display:block;font-size:24px;margin-top:2px}
.contact-tab{position:absolute;left:576px;top:14px;width:556px;height:42px;background:var(--green);
  clip-path:polygon(0 0,100% 0,96% 100%,4% 100%);display:flex;align-items:center;gap:30px;padding-left:52px;color:var(--white);font-size:14px;font-weight:600}
.contact-tab .item{display:flex;align-items:center;gap:9px}
.contact-tab .social{display:flex;gap:4px;margin-left:12px}
.contact-tab .social span{width:18px;height:18px;border:1.5px solid var(--white);border-radius:50%}

.main-nav{height:45px;background:var(--nav);display:flex;padding-left:268px}
.main-nav a{display:flex;align-items:center;padding:0 18px;color:#b9c2c0;font-size:13px;font-weight:600;text-decoration:none;text-transform:uppercase}
.main-nav a.active{background:var(--green);color:var(--white)}

.hero{position:relative;height:508px;background:
  radial-gradient(ellipse at 60% 22%,#4fe6a0 0%,rgba(40,180,120,.6) 25%,rgba(10,60,70,0) 55%),
  linear-gradient(180deg,#0b2030 0%,#12463f 30%,#1a8a6a 55%,#0f4a48 75%,#0a2a30 100%)}
.hero .tagline{position:absolute;left:0;right:0;top:388px;text-align:center;font-family:"Ropa Sans",Arial,sans-serif;font-size:56px;color:var(--white);transform:translateY(-268px)}
.dot{display:inline-block;width:14px;height:14px;border:3px solid var(--green);border-radius:50%;margin:0 10px;vertical-align:middle}

/* section titles */
.section-title{display:flex;align-items:center;justify-content:center;gap:16px;font-family:"Ropa Sans",Arial,sans-serif;font-size:31px;color:var(--ink)}
.section-title::before,.section-title::after{content:"";width:60px;height:1px;background:var(--rule)}
.section-title em{font-style:normal;color:var(--green)}
.title-mark{width:26px;height:26px}

/* who we are */
.who{height:572px;padding-top:58px}
.cards{display:flex;width:1100px;margin:28px auto 0}
.card{flex:1;padding:0 26px;border-left:1px solid var(--rule);height:380px}
.card:first-child{border-left:none}
.badge{display:block;width:190px;height:40px;margin:0 auto;background:var(--green);color:var(--white);border-radius:8px;text-align:center;line-height:40px;font-weight:700;font-size:15px;box-shadow:0 8px 6px -6px rgba(0,0,0,.3)}
.card-visual{height:188px;margin-top:14px}
.card h3{margin-top:26px;font-size:19px;font-weight:700;color:var(--ink)}
.card p{margin-top:16px;font-size:14px;line-height:1.45}

/* what we do */
.what{height:540px;background:var(--panel);padding-top:62px}
.columns{display:flex;width:1100px;margin:38px auto 0}
.column{flex:1;padding:0 26px;border-left:1px solid var(--rule);height:292px}
.column:first-child{border-left:none}
.column h3{font-family:"Ropa Sans",Arial,sans-serif;font-weight:400;font-size:21px;color:var(--ink)}
.column h3 em{font-style:normal;color:var(--green)}
.column ul{list-style:none;margin-top:22px}
.column li{position:relative;padding-left:38px;margin-bottom:16px;font-size:14px;line-height:1.45}
.column li::before{content:"";position:absolute;left:0;top:12px;width:10px;height:10px;border:3px solid var(--green);border-radius:50%}
.column li::after{content:"";position:absolute;left:-4px;top:3px;width:5px;height:5px;background:var(--green);border-radius:50%}
.button{display:block;width:190px;height:42px;margin:30px auto 0;background:var(--green);color:var(--white);text-align:center;line-height:42px;border-radius:8px;font-weight:700;font-size:15px;text-decoration:none;box-shadow:0 8px 6px -6px rgba(0,0,0,.3)}

/* different */
.different{position:relative;height:472px;padding-top:58px}
.diagram{position:absolute;left:0;top:0;width:1172px;height:472px}
.trait{position:absolute;font-size:14px;font-weight:600;color:var(--ink);line-height:1.4}
.trait strong{font-family:"Ropa Sans",Arial,sans-serif;font-weight:400;font-size:19px}
.trait.left{text-align:right;width:330px}
.trait.right{text-align:left;width:330px}
.hub-name{position:absolute;left:486px;top:237px;width:200px;text-align:center;font-family:"Nunito",Arial,sans-serif;font-weight:800;color:var(--ink);font-size:34px;line-height:.95}
.hub-name span{display:block;font-size:21px}

/* message */
.message{height:344px;background:var(--panel);padding-top:56px}
.contact-form{position:relative;width:732px;margin:40px auto 0;height:170px}
.field{position:absolute;background:var(--white);border:none;font:15px "Open Sans",Arial,sans-serif;color:#555;padding:10px 20px;width:360px;height:44px}
.field.message-box{left:372px;top:0;height:102px}
.send{position:absolute;left:372px;top:114px;width:126px;height:46px;background:#111;color:var(--white);font:700 16px "Open Sans",Arial,sans-serif;border:none;letter-spacing:1px}

/* footer */
.site-footer{position:relative;height:139px}
.site-footer .brand{left:28px;top:34px}
.footer-tag{position:absolute;left:221px;top:46px;font-family:"Ropa Sans",Arial,sans-serif;font-size:27px;color:var(--green)}
.footer-tag .dot{width:10px;height:10px;border-width:2px;margin:0 6px}
.footer-nav{position:absolute;right:24px;top:58px;display:flex;gap:20px}
.footer-nav a{font-size:13px;color:var(--muted);text-decoration:none;text-transform:uppercase;font-weight:600}
.footer-nav a.active{color:var(--green)}
.copyright{height:37px;background:var(--green);color:var(--white);text-align:center;line-height:37px;font-size:11px;font-weight:700;text-transform:uppercase}
</style>
</head>
<body>
<div class="page">

  <header class="site-header">
    <div class="brand"><span class="line1">Drabek</span><span class="line2">Partners</span></div>
    <div class="contact-tab">
      <span class="item">
        <svg width="20" height="20" viewBox="0 0 20 20"><circle cx="10" cy="10" r="9" fill="none" stroke="#fff" stroke-width="1.5"/><path d="M6.5 5.5l2 .3.6 2.2-1.1 1a6 6 0 0 0 3 3l1-1.1 2.2.6.3 2-1.4 1.2C9.8 14.5 5.5 10.2 5.3 6.9z" fill="#fff"/></svg>
        1-800-555-0142
      </span>
      <span class="item">
        <svg width="20" height="20" viewBox="0 0 20 20"><circle cx="10" cy="10" r="9" fill="none" stroke="#fff" stroke-width="1.5"/><rect x="5.5" y="7" width="9" height="6.5" fill="none" stroke="#fff" stroke-width="1.3"/><path d="M5.5 7l4.5 3.5L14.5 7" fill="none" stroke="#fff" stroke-width="1.3"/></svg>
        info@drabekpartners.com
      </span>
      <span class="social"><span></span><span></span><span></span></span>
    </div>
  </header>

  <nav class="main-nav">
    <a class="active" href="#home">Home</a>
    <a href="#who">Who We Are</a>
    <a href="#what">What We Do</a>
    <a href="#different">What Makes Us Different</a>
    <a href="#contact">Contact</a>
  </nav>

  <section class="hero" id="home" role="img" aria-label="Northern lights glowing green over a calm lake with a forested shoreline">
    <p class="tagline">people<span class="dot"></span>capital<span class="dot"></span>strategy</p>
  </section>

  <section class="who" id="who">
    <h2 class="section-title"><svg class="title-mark" viewBox="0 0 26 26"><circle cx="5" cy="5" r="3" fill="#27b27f"/><circle cx="16" cy="16" r="6.5" fill="none" stroke="#27b27f" stroke-width="3.5"/></svg><span>Who <em>We Are</em></span></h2>
    <div class="cards">
      <article class="card">
        <span class="badge">Direct</span>
        <div class="card-visual" role="img" aria-label="Chrome spheres arranged in a V formation led by a blue sphere" style="background:radial-gradient(circle at 50% 70%,#9fb9d8 0,#d6dbe0 30%,#fdfdfd 70%)"></div>
        <h3>Leading Directors</h3>
        <p>We identify and connect appropriate resources to the relevant opportunity points to create business momentum.</p>
      </article>
      <article class="card">
        <span class="badge">Human</span>
        <div class="card-visual" role="img" aria-label="Golden figure climbing blue steps ahead of a grey crowd" style="background:linear-gradient(160deg,#ffffff 0,#e9ecef 45%,#7fb4e6 80%,#f2c94c 100%)"></div>
        <h3>Leading Motivators</h3>
        <p>We generate inspiration, motivation and activation through our shared passion for success and converting opportunity to results.</p>
      </article>
      <article class="card">
        <span class="badge">Energy</span>
        <div class="card-visual" role="img" aria-label="Chalkboard with light bulb sketches and a hand drawing" style="background:linear-gradient(135deg,#2f5a40 0,#3e6e50 60%,#5b8a66 100%)"></div>
        <h3>Leading Energisers</h3>
        <p>Together, our collective combination of business capabilities forge a powerful, visible impact – delivered with efficiency and effectiveness.</p>
      </article>
    </div>
  </section>

  <section class="what" id="what">
    <h2 class="section-title"><svg class="title-mark" viewBox="0 0 26 26"><circle cx="5" cy="5" r="3" fill="#27b27f"/><circle cx="16" cy="16" r="6.5" fill="none" stroke="#27b27f" stroke-width="3.5"/></svg><span>What <em>We Do</em></span></h2>
    <div class="columns">
      <div class="column">
        <h3>We Build <em>Ventures</em></h3>
        <ul>
          <li>We invest people and financial capital in ventures that have potential.</li>
          <li>We create joint ventures with partners that will bring synergies to our house of brands.</li>
          <li>We confidently venture into new markets, industries and initiatives with entrepreneurial energy.</li>
        </ul>
      </div>
      <div class="column">
        <h3>We are <em>Energising Opportunities</em></h3>
        <ul>
          <li>Our passion for business, performance and success energises our ventures, our people, and the opportunities we invest in.</li>
          <li>Our vision and focus energises people to see beyond what is, to what could be, opening up new opportunities.</li>
          <li>The opportunities we create energise existing ventures with positive momentum.</li>
        </ul>
      </div>
      <div class="column">
        <h3>We Deliver <em>People</em></h3>
        <ul>
          <li>We invest in our people supporting their personal and professional growth.</li>
          <li>We invest our people and financial capital into partnerships driving success.</li>
          <li>We provide the strategic leadership, direction and vision with a strategy of empowering our ventures.</li>
        </ul>
      </div>
    </div>
    <a class="button" href="#contact">Learn More</a>
  </section>

  <section class="different" id="different">
    <svg class="diagram" viewBox="0 0 1172 472" aria-hidden="true">
      <g stroke="#27b27f" stroke-width="1.5" fill="none">
        <path d="M392 178 L392 224 L500 224"/>
        <path d="M772 178 L772 224 L672 224"/>
        <path d="M392 312 L392 280 L500 280"/>
        <path d="M772 312 L772 280 L672 280"/>
      </g>
      <circle cx="586" cy="265" r="96" fill="#fff" stroke="#e2e2e2" stroke-width="6"/>
      <g fill="#fff" stroke="#27b27f" stroke-width="3">
        <circle cx="392" cy="178" r="38"/><circle cx="772" cy="178" r="38"/>
        <circle cx="392" cy="350" r="38"/><circle cx="772" cy="350" r="38"/>
      </g>
      <g fill="none" stroke="#27b27f" stroke-width="3">
        <path d="M380 166 a16 16 0 1 0 12 -5"/><path d="M392 170 v9 l6 5"/><path d="M376 160 l4 6 6-4"/>
        <rect x="754" y="162" width="22" height="22"/><rect x="766" y="174" width="22" height="22"/>
        <path d="M760 364 v-14 M768 364 v-20 M776 364 v-26 M784 364 v-32"/>
        <path d="M756 336 l12-8 6 4 12-10"/>
      </g>
      <g fill="#27b27f">
        <circle cx="392" cy="340" r="5"/><path d="M382 362 a10 10 0 0 1 20 0z"/>
        <circle cx="378" cy="344" r="4"/><path d="M370 360 a8 8 0 0 1 14 -3v5z"/>
        <circle cx="406" cy="344" r="4"/><path d="M414 360 a8 8 0 0 0 -14 -3v5z"/>
      </g>
      <text x="586" y="60" font-family="Ropa Sans, Arial, sans-serif" font-size="0"> </text>
    </svg>
    <h2 class="section-title" style="position:relative"><svg class="title-mark" viewBox="0 0 26 26"><circle cx="5" cy="5" r="3" fill="#27b27f"/><circle cx="16" cy="16" r="6.5" fill="none" stroke="#27b27f" stroke-width="3.5"/></svg><span>What Makes Us <em>Different</em></span></h2>
    <p class="trait left" style="left:12px;top:152px"><strong>RESPONSIVE</strong> - Mobile Agility<br>We act and respond swiftly –<br>but responsibly</p>
    <p class="trait right" style="left:832px;top:162px"><strong>TRANSPARENT</strong> - we champion our values<br>Connections – leadership – success</p>
    <p class="trait left" style="left:12px;top:326px"><strong>SUPPORTIVE</strong> - welcoming family<br>Considerate and respectful of the<br>importance of lifestyle balance</p>
    <p class="trait right" style="left:832px;top:336px"><strong>PERFORMANCE</strong> - network integrity<br>Quality, responsibility and consideration</p>
    <div class="hub-name">Drabek<span>Partners</span></div>
  </section>

  <section class="message" id="contact">
    <h2 class="section-title"><svg class="title-mark" viewBox="0 0 26 26"><circle cx="5" cy="5" r="3" fill="#27b27f"/><circle cx="16" cy="16" r="6.5" fill="none" stroke="#27b27f" stroke-width="3.5"/></svg><span>Send a <em>Message</em></span></h2>
    <form class="contact-form">
      <input class="field" style="left:0;top:0" placeholder="Name">
      <input class="field" style="left:0;top:58px" placeholder="Email">
      <input class="field" style="left:0;top:116px" placeholder="Phone">
      <textarea class="field message-box" placeholder="Message"></textarea>
      <button class="send" type="submit">SEND</button>
    </form>
  </section>

  <footer class="site-footer">
    <div class="brand"><span class="line1">Drabek</span><span class="line2">Partners</span></div>
    <p class="footer-tag">people<span class="dot"></span>capital<span class="dot"></span>strategy</p>
    <nav class="footer-nav">
      <a class="active" href="#home">Home</a>
      <a href="#who">Who We Are</a>
      <a href="#what">What We Do</a>
      <a href="#different">What Makes Us Different</a>
      <a href="#contact">Contact</a>
    </nav>
  </footer>
  <div class="copyright">Copyright © 2017 Drabek Partners. All rights reserved.</div>

</div>
</body>
</html>
```